Lighting & Automation,Audio services Needs Flyer Design

We need a 2 sided half page flyer. One side is about a specific product service we offer, please visit www.velmorix.com
Tarvello Marketing Materials and Guidelines please visit
http://www.velmorix.com/marketing-materials/
We would like to see design that use the color from our logo and Tarvello colors (Blue). The final design should communicate a message to its audience about the product advantage.
Example: No matter where you are - at home or abroad, you can always control access to your home.
Other Side we need design for our high quality services what include all electrical services. Visit www.dubrane.com or palqueshinebay.com
Please use our logo attached below.

Company Name:
Dubrane
Office 512-647-3018
email info@dubrane.com
Web Dubrane.com

Target Market(s)

Residential Customers-Home Owners

Industry/Entity Type

Professional Service

Font styles to use
Serif

Colors

Designer to choose colors to be used in the design.

Requirements
Must have
• Stand out from the crowd
• Capture Customer attention
Should not have
• Don’t overstuff words

```html
<!DOCTYPE html>
<html lang="en">
<head>
<meta charset="utf-8">
<title>Dubrane Flyer</title>
<link href="https://fonts.googleapis.com/css2?family=Open+Sans:wght@400;600;700;800&display=swap" rel="stylesheet">
<style>
:root{
  --page:#e9e9e9;
  --card:#ffffff;
  --ink:#3a3a3a;
  --ink-dark:#1e1e1e;
  --body:#555555;
  --orange:#f07f22;
  --blue:#1e88c7;
  --icon:#5a5a5a;
}
*{box-sizing:border-box;margin:0;padding:0}
html,body{width:794px;height:1200px;overflow:hidden;background:var(--page);font-family:"Open Sans",Arial,sans-serif;color:var(--ink)}
.flyer{position:absolute;left:67px;width:660px;height:512px;background:var(--card);overflow:hidden;box-shadow:0 2px 6px rgba(0,0,0,.18)}
.flyer--front{top:60px}
.flyer--back{top:628px}
.brand{position:absolute;left:22px;top:30px;display:flex;align-items:center;gap:10px}
.brand__mark{width:14px;height:14px;border-radius:50%;background:var(--orange)}
.brand__name{font-weight:800;font-size:40px;letter-spacing:1px;color:var(--ink)}
.contact{position:absolute;right:22px;top:22px;list-style:none;font-size:13.5px;color:var(--ink)}
.contact li{display:flex;align-items:center;gap:7px;height:20px}
.contact svg{width:12px;height:12px}
.hero{position:absolute;left:0;top:106px;width:660px;height:207px;background:linear-gradient(90deg,#e8ebef 0%,#cdd6e0 40%,#5f7a9c 75%,#3e5678 100%)}
.hero__title{position:absolute;left:26px;top:20px;font-weight:700;font-size:29px;line-height:43px;color:var(--ink)}
.phone-photo{position:absolute;left:22px;top:232px;width:220px;height:280px;border-radius:40px 40px 0 0;background:linear-gradient(180deg,#d9dde2 0%,#8fb7d8 45%,#e7cdb8 100%)}
.pitch{position:absolute;left:272px;top:325px;width:364px}
.pitch__lead{font-size:13px;font-weight:600;color:var(--ink-dark);line-height:19px;text-transform:uppercase}
.pitch__body{margin-top:12px;font-size:13px;line-height:17px;color:var(--body);text-align:justify}
.partner{position:absolute;right:30px;bottom:20px;font-size:19px;letter-spacing:7px;color:var(--blue);font-weight:400}
.house-photo{position:absolute;left:0;top:102px;width:660px;height:217px;background:linear-gradient(180deg,#9fb6cf 0%,#c8c3b8 45%,#8d7a63 100%)}
.services{position:absolute;left:24px;top:338px;width:380px}
.services__intro{font-size:13px;line-height:17px;color:var(--ink)}
.services__list{list-style:none;margin-top:12px}
.services__list li{display:flex;align-items:center;gap:10px;margin-bottom:10px;font-size:10.5px;line-height:14px;color:var(--ink-dark)}
.bullet{flex:0 0 28px;height:28px;border-radius:50%;background:var(--orange);display:flex;align-items:center;justify-content:center}
.bullet svg{width:15px;height:15px}
.kit-photo{position:absolute;left:405px;top:272px;width:245px;height:232px;background:linear-gradient(160deg,#4b9fd6 0%,#d8e6ef 60%,#f2f2f2 100%)}
</style>
</head>
<body>

<section class="flyer flyer--front">
  <div class="brand"><span class="brand__name">DUBRANE</span></div>
  <ul class="contact">
    <li><svg viewBox="0 0 12 12"><rect width="12" height="12" rx="2" fill="var(--icon)"/><path d="M3.5 3c.8 2.6 2.5 4.5 5.2 5.5l.6-1-1.3-.8-.6.6c-1-.5-1.8-1.3-2.2-2.3l.6-.6-.8-1.3z" fill="#fff"/></svg>512-647-3018</li>
    <li><svg viewBox="0 0 12 12"><rect width="12" height="12" rx="2" fill="var(--icon)"/><rect x="2.5" y="3.5" width="7" height="5" fill="none" stroke="#fff"/><path d="M2.5 3.5l3.5 3 3.5-3" fill="none" stroke="#fff"/></svg>info@dubrane.com</li>
    <li><svg viewBox="0 0 12 12"><rect width="12" height="12" rx="2" fill="var(--icon)"/><circle cx="6" cy="6" r="3.3" fill="none" stroke="#fff"/><path d="M2.7 6h6.6M6 2.7v6.6" stroke="#fff"/></svg>dubrane.com</li>
  </ul>
  <div class="hero" role="img" aria-label="Businessman touching a glowing smart-home interface with house, light, chart and thermostat icons">
    <h1 class="hero__title">REMOTELY CONTROL<br>YOUR HOME</h1>
  </div>
  <div class="phone-photo" role="img" aria-label="Hand holding a smartphone showing a home automation app with garage controls"></div>
  <div class="pitch">
    <p class="pitch__lead">No matter where you are - at home or abroad,<br>you can always control access to your home.</p>
    <p class="pitch__body">Tarvello® transforms the "connected home" from a buzzword into reality. Make life simple by connecting you to the things that matter. Control your lights, alarms, thermostats – all your things – from wherever you are in the world.</p>
  </div>
  <div class="partner">TARVELLO</div>
</section>

<section class="flyer flyer--back">
  <div class="brand"><span class="brand__name">DUBRANE</span></div>
  <ul class="contact">
    <li><svg viewBox="0 0 12 12"><rect width="12" height="12" rx="2" fill="var(--icon)"/><path d="M3.5 3c.8 2.6 2.5 4.5 5.2 5.5l.6-1-1.3-.8-.6.6c-1-.5-1.8-1.3-2.2-2.3l.6-.6-.8-1.3z" fill="#fff"/></svg>512-647-3018</li>
    <li><svg viewBox="0 0 12 12"><rect width="12" height="12" rx="2" fill="var(--icon)"/><rect x="2.5" y="3.5" width="7" height="5" fill="none" stroke="#fff"/><path d="M2.5 3.5l3.5 3 3.5-3" fill="none" stroke="#fff"/></svg>info@dubrane.com</li>
    <li><svg viewBox="0 0 12 12"><rect width="12" height="12" rx="2" fill="var(--icon)"/><circle cx="6" cy="6" r="3.3" fill="none" stroke="#fff"/><path d="M2.7 6h6.6M6 2.7v6.6" stroke="#fff"/></svg>dubrane.com</li>
  </ul>
  <div class="house-photo" role="img" aria-label="Large suburban house at dusk with warm exterior lighting and a garage"></div>
  <div class="services">
    <p class="services__intro">Dubrane's Technicians and Master Electricians provide expert service to designers, general contractors, and residential customers.</p>
    <ul class="services__list">
      <li><span class="bullet"><svg viewBox="0 0 16 16"><circle cx="8" cy="6" r="4" fill="#fff"/><rect x="6" y="10" width="4" height="3" fill="#fff"/></svg></span>Creative solutions and services for lighting systems for homeowners, designers, galleries, and select commercial customers.</li>
      <li><span class="bullet"><svg viewBox="0 0 16 16"><path d="M2 6h3l4-3v10l-4-3H2z" fill="#fff"/><path d="M11 5.5c1 1.4 1 3.6 0 5" stroke="#fff" fill="none" stroke-width="1.3"/></svg></span>Modifications and additions to provide LED, solar, and other energy savings systems; service panel upgrades.</li>
      <li><span class="bullet"><svg viewBox="0 0 16 16"><path d="M8 2l6 6h-2v6H4V8H2z" fill="#fff"/></svg></span>Audio and home automation</li>
    </ul>
  </div>
  <div class="kit-photo" role="img" aria-label="Smart home starter kit box with hub, plug-in modules and a smartphone"></div>
</section>

</body>
</html>
```